A new presentation to our clients

we are a Real Estate agency, our website is www.lumibrasa.com and it’s time to have a new, fashion and remarcable Business Card. we want to differentiate ourselves from other companies so we want a business card that differentiates us. we want the business card to impact our customers. in the competitive market that we have today, we have to be different and it is this difference that we seek

Target Market(s)

Real Estate Clients

Contact Information for Business Card

We search a totaly diferent card from the usual

Font styles to use
Sans Serif

Colors
e34197

Requirements
Must have
• Logo, adress, phone contact, e-mail, photo, and our website
Nice to have
• We would like to see a modern business card
Should not have
• Houses or building draws

```html
<!DOCTYPE html>
<html lang="pt">
<head>
<meta charset="utf-8">
<title>Lumibrasa – Business Card</title>
<link href="https://fonts.googleapis.com/css2?family=Open+Sans:wght@400;600&family=Roboto:wght@500&display=swap" rel="stylesheet">
<style>
  :root {
    --brand-pink: #e5236c;
    --paper: #ffffff;
    --ink: #3a3a3a;
    --tagline: #f6d3e0;
    --backdrop: #7a7a7a;
  }
  * { margin: 0; padding: 0; box-sizing: border-box; }
  html, body { width: 1200px; height: 802px; overflow: hidden; }
  body { background: var(--backdrop); position: relative; font-family: "Open Sans", sans-serif; }

  .card {
    position: absolute;
    top: 274px;
    width: 442px;
    height: 264px;
    box-shadow: 2px 3px 6px rgba(0,0,0,0.45);
  }

  /* Front */
  .card-front { left: 136px; background: var(--paper); }
  .side-band {
    position: absolute; left: 0; top: 0; bottom: 0; width: 55px;
    background: var(--brand-pink);
  }
  .side-rule {
    position: absolute; left: 57px; top: 0; bottom: 0; width: 3px;
    background: var(--brand-pink);
  }
  .wordmark {
    position: absolute;
    font-family: "Open Sans", sans-serif;
    font-weight: 600;
    letter-spacing: 0.5px;
    line-height: 1;
    white-space: nowrap;
  }
  .card-front .wordmark {
    right: 26px; top: 38px;
    font-size: 44px;
    color: var(--brand-pink);
  }
  .holder { position: absolute; left: 86px; top: 110px; }
  .holder-name {
    font-family: "Roboto", sans-serif;
    font-weight: 500;
    font-size: 16px;
    color: var(--brand-pink);
    line-height: 18px;
  }
  .holder-role { font-size: 13px; color: var(--ink); line-height: 15px; }

  .contacts { position: absolute; left: 86px; top: 147px; list-style: none; }
  .contacts li {
    display: flex; align-items: center;
    font-size: 13px; line-height: 15.7px; color: var(--ink);
    white-space: nowrap;
  }
  .contacts svg { width: 10px; height: 10px; margin-right: 5px; fill: var(--brand-pink); flex: none; }

  .address {
    position: absolute; left: 86px; top: 214px;
    font-style: normal; font-size: 13px; line-height: 15.5px; color: var(--ink);
  }

  /* Back */
  .card-back { left: 624px; background: var(--brand-pink); }
  .card-back .wordmark {
    left: 0; right: 0; top: 114px;
    text-align: center;
    font-size: 44px;
    color: var(--paper);
  }
  .tagline {
    position: absolute; left: 0; right: 0; top: 172px;
    text-align: center;
    font-family: "Roboto", sans-serif;
    font-weight: 500;
    font-size: 12.5px;
    letter-spacing: 0.9px;
    color: var(--tagline);
    white-space: nowrap;
  }
</style>
</head>
<body>

<section class="card card-front">
  <div class="side-band"></div>
  <div class="side-rule"></div>
  <div class="wordmark">Lumibrasa</div>

  <div class="holder">
    <p class="holder-name">RAFAEL MENDES</p>
    <p class="holder-role">Managing Director</p>
  </div>

  <ul class="contacts">
    <li>
      <svg viewBox="0 0 10 10" aria-hidden="true"><path d="M1 3.2C1 2 2 1.2 5 1.2S9 2 9 3.2L7.4 4 6.8 3H3.2L2.6 4zM2.5 4.6h5L8.5 8.8h-7z"/></svg>
      (+351) 220 418 360
    </li>
    <li>
      <svg viewBox="0 0 10 10" aria-hidden="true"><path d="M2.5 1h5v2.2h-5zM1 3.8h8v3.4H7.6V6H2.4v1.2H1zM2.9 6.6h4.2V9H2.9z"/></svg>
      (+351) 220 418 369
    </li>
    <li>
      <svg viewBox="0 0 10 10" aria-hidden="true"><path d="M1 2.4h8v.6L5 5.6 1 3zM1 3.9l4 2.6 4-2.6V7.8H1z"/></svg>
      geral@lumibrasa.com
    </li>
    <li>
      <svg viewBox="0 0 10 10" aria-hidden="true"><circle cx="5" cy="5" r="4.2"/><path d="M3 3.4l1.4-.6 1 1-.6 1.2 1 1.4-.6 1.6-1.2-1.4-.2-1.4z" fill="#fff"/></svg>
      www.lumibrasa.com
    </li>
  </ul>

  <address class="address">
    Rua das Acácias, 148<br>
    4450-212, Matosinhos
  </address>
</section>

<section class="card card-back">
  <div class="wordmark">Lumibrasa</div>
  <p class="tagline">YOUR NEXT HOME STARTS HERE</p>
</section>

</body>
</html>
```